Veltrane Group Business Card Design

The CEO is looking for a new trendy look for his business card.
You can stay with current branding or come up with something new/creative. It can be 3D, including Medical Office buildings. You can use our logo in a variety of colors. Please include name, title, company name, company website, email address, cell number

Target Market(s)

Real Estate Development and Construction

Industry/Entity Type

Health care real estate

Contact Information for Business Card

Rohesh Kamdar, CEO M-604.781.2249 E-roheshkamdar@veltrane.com Address:4180 Lindqvist Ave, Tampa, FL 33482 www.veltrane.com

Font styles to use
Other font styles liked:
• Be creative

Requirements
Must have
• Creative, trendy look
Nice to have
• Please go to our website to get a feel- www. veltrane.com
Should not have
• small fonts

```html
<!DOCTYPE html>
<html lang="en">
<head>
<meta charset="utf-8">
<title>Veltrane Group – Business Card</title>
<link href="https://fonts.googleapis.com/css2?family=Arimo:wght@400;700&display=swap" rel="stylesheet">
<style>
  :root {
    --brand-red: #b21f2b;
    --brand-red-light: #c8303d;
    --brand-navy: #1c2f55;
    --paper: #ffffff;
    --backdrop: #e9e9ec;
  }
  * { box-sizing: border-box; margin: 0; padding: 0; }
  html, body { width: 1200px; height: 874px; overflow: hidden; }
  body {
    background: var(--backdrop);
    font-family: "Arimo", Arial, sans-serif;
    display: flex;
    flex-direction: column;
    align-items: center;
    justify-content: center;
    gap: 40px;
  }
  .card {
    position: relative;
    width: 640px;
    height: 366px;
    border-radius: 22px;
    overflow: hidden;
    background: var(--brand-red);
    box-shadow: 0 8px 24px rgba(0,0,0,0.18);
  }

  /* Front */
  .card-front .wordmark {
    position: absolute;
    left: 0; right: 0; top: 130px;
    text-align: center;
    font-weight: 700;
    font-size: 60px;
    color: var(--brand-red-light);
  }
  .card-front .site {
    position: absolute;
    left: 0; right: 0; bottom: 44px;
    text-align: center;
    color: var(--paper);
    font-size: 15px;
    letter-spacing: 4px;
  }

  /* Back */
  .card-back .shape { position: absolute; inset: 0; }
  .card-back .person {
    position: absolute; left: 30px; top: 36px; color: var(--paper);
  }
  .person .name { font-size: 26px; font-weight: 700; }
  .person .title { font-size: 14px; margin-top: 2px; }
  .card-back .address {
    position: absolute; left: 30px; top: 180px;
    color: var(--paper); font-size: 16px; line-height: 1.3;
  }
  .card-back .contacts {
    position: absolute; left: 26px; top: 250px;
    list-style: none; color: var(--paper); font-size: 15px;
  }
  .contacts li { display: flex; align-items: center; gap: 9px; height: 24px; }
  .contacts svg { width: 14px; height: 14px; flex: none; }
  .card-back .wordmark {
    position: absolute; left: 300px; right: 0; top: 160px;
    text-align: center;
    font-weight: 700; font-size: 38px;
    color: var(--brand-red);
  }
</style>
</head>
<body>

  <section class="card card-front" aria-label="Card front">
    <div class="wordmark">Veltrane Group</div>
    <div class="site">www.veltrane.com</div>
  </section>

  <section class="card card-back" aria-label="Card back">
    <svg class="shape" viewBox="0 0 640 366" preserveAspectRatio="none" aria-hidden="true">
      <path d="M388 0 C268 70 228 250 288 366 L300 366 C244 250 284 70 404 0 Z" fill="var(--brand-navy)"/>
      <path d="M404 0 C284 70 244 250 300 366 L640 366 L640 0 Z" fill="var(--paper)"/>
    </svg>

    <div class="person">
      <div class="name">Rohesh Kamdar</div>
      <div class="title">CEO</div>
    </div>

    <div class="address">4180 Lindqvist Ave, Tampa<br>FL 33482</div>

    <ul class="contacts">
      <li>
        <svg viewBox="0 0 24 24" aria-hidden="true"><path fill="#fff" d="M6.6 10.8a15.1 15.1 0 0 0 6.6 6.6l2.2-2.2a1 1 0 0 1 1-.25 11.4 11.4 0 0 0 3.6.57 1 1 0 0 1 1 1V20a1 1 0 0 1-1 1A17 17 0 0 1 3 4a1 1 0 0 1 1-1h3.5a1 1 0 0 1 1 1c0 1.25.2 2.45.57 3.6a1 1 0 0 1-.25 1Z"/></svg>
        604.781.2249
      </li>
      <li>
        <svg viewBox="0 0 24 24" aria-hidden="true"><rect x="2" y="5" width="20" height="14" rx="1.5" fill="#fff"/><path d="M3 6l9 7 9-7" fill="none" stroke="var(--brand-red)" stroke-width="2"/></svg>
        roheshkamdar@veltrane.com
      </li>
      <li>
        <svg viewBox="0 0 24 24" aria-hidden="true"><circle cx="12" cy="12" r="10" fill="#fff"/><path d="M2 12h20M12 2c3 3 3 17 0 20M12 2c-3 3-3 17 0 20" fill="none" stroke="var(--brand-red)" stroke-width="1.6"/></svg>
        www.veltrane.com
      </li>
    </ul>

    <div class="wordmark">Veltrane Group</div>
  </section>

</body>
</html>
```